Orvane Thinner Logo and Packaging Design

We are seeking a striking and professional logo and packaging design for our new product line, Orvane Thinner. This logo will be used on the packaging for three different sizes of half-transparent carboys: 1L, 4L, and 20L. Orvane Thinner is a high-quality solvent brand known for its excellent solvency, fast-drying properties, and pleasant smell. The logo should feature an eagle motif to symbolize power and precision, and our slogan, "FLY WITH QUALITY." The design should be suitable for placement on hardware store and warehouse shelves. Additionally, we need the designer to create an eagle logo to accompany the packaging.

Packaging Dimensions:
1L Carboy:
Front: 71mm height x 142mm width
Side: 71mm height x 73mm width
4L Carboy:
Front: 160mm height x 170mm width
Side: 160mm height x 120mm width
20L Carboy:
Front: 245mm height x 190mm width
Side: 215mm height x 190mm width
Front Label Requirements:

Product Name: Thinner QXR
Volume: 20L
Precautionary Statements:
Keep Away from Sources of ignition - No Smoking
Avoid Contact with Eyes
Do Not Empty into Drains or Sewers
Take Precautionary Measures Against Static Discharge
Hazard Statements:
Flammable Liquid and Vapor
May be fatal if swallowed or enters Airways
Causes Skin Irritation
Causes Serious Eye Irritation
Causes Damage to Organs if Prolonged or Repeated Exposure
Hazard Pictograms: (Include relevant hazard symbols)
Design Requirements:

Logo: Eagle motif (to be designed by the designer)
Slogan: FLY WITH QUALITY
Color Scheme: Designer to recommend (should be striking and professional for retail display)

Please see my latest picture. Kindly note the packaging is in Plastic Carboy (not in metal tin as per PS).

Eagle to be more majestic and bigger (as if soaring in the sky).
Singapore landscape as background to have Singapore identity such as KTR, Corvale wheel, terrace at the cove etc.

Eagle to be more majestic and bigger, wings to spread wide.
We not want it to be of photo style, but more on a cartoon style. Please see my latest file uploaded.

Target Market(s)

Our target market includes painting companies, construction companies, direct household consumers, and industrial users who require high-quality solvents for various applications.

Industry/Entity Type

Chemical, spray paint and painting, household, industrial

Requirements
Must have
• Professional and Striking Design: Eye-catching and professional packaging for retail shelves. Eagle Logo: A strong, precise eagle logo. Slogan: "FLY WITH QUALITY" prominently displayed. Clear Precautionary and Hazard Statements: Important safety information and pictograms. Volume Indication: Clearly marked (e.g., 1L, 4L, 20L). Eagle to be more majestic and bigger (as if soaring in the sky). Singapore landscape as background to have Singapore identity such as KTR, Corvale wheel, terrace at the cove etc.
Nice to have
• Color Scheme Recommendations: Suggestions for a professional, striking color scheme. Versatility: Design elements adaptable across different sizes of packaging. Environmentally Friendly Elements: Indications of sustainability or eco-friendliness in the design.
Should not have
• Overly Complex Designs: Avoid cluttered or overly intricate designs that detract from readability. Inconsistent Branding: Ensure all elements are cohesive and align with the brand identity.

```html
<!DOCTYPE html>
<html lang="en">
<head>
<meta charset="utf-8">
<title>Orvane Thinner – Thinner QXR 20L Label</title>
<link href="https://fonts.googleapis.com/css2?family=Montserrat:wght@400;600;700;800&display=swap" rel="stylesheet">
<style>
  :root {
    --backdrop: #dc7b53;
    --label-bg: #ececec;
    --brand-orange: #d9714f;
    --ink-grey: #555555;
    --rust: #a84b34;
    --rust-deep: #8f3d2a;
    --skyline-light: #c9a79a;
    --skyline-mid: #a8705a;
    --skyline-dark: #7d4a38;
    --warning-yellow: #f2c230;
    --white: #ffffff;
  }
  * { box-sizing: border-box; margin: 0; padding: 0; }
  html, body {
    width: 1200px; height: 718px; overflow: hidden;
    background: var(--backdrop);
    font-family: "Montserrat", Arial, sans-serif;
  }
  .label {
    position: absolute; left: 360px; top: 24px;
    width: 480px; height: 670px;
    background: var(--label-bg);
    display: flex; flex-direction: column;
    padding: 26px 24px 0;
  }
  .product-title {
    display: flex; align-items: center; justify-content: space-between; gap: 14px;
  }
  .product-title .bar { flex: 0 0 46px; height: 12px; background: var(--brand-orange); }
  .product-title h1 {
    font-weight: 800; font-size: 40px; color: var(--ink-grey);
    letter-spacing: 0.5px; white-space: nowrap;
  }
  .brand-row {
    display: flex; align-items: center; gap: 16px; margin: 26px 0 0 8px;
  }
  .brand-row .brand-mark { width: 22px; height: 22px; background: var(--brand-orange); }
  .brand-row .brand-name {
    font-weight: 600; font-size: 25px; letter-spacing: 3px; color: var(--ink-grey);
  }
  .eagle-illustration {
    margin-top: 26px; height: 232px;
    background: linear-gradient(160deg, #e29a7c 0%, var(--brand-orange) 60%);
    border-radius: 4px;
  }
  .skyline {
    position: relative; height: 128px; margin-top: 10px;
    background: linear-gradient(180deg, var(--skyline-light) 0%, var(--skyline-mid) 60%, var(--skyline-dark) 100%);
  }
  .slogan-ribbon {
    position: absolute; left: 72px; top: 38px; width: 346px; height: 40px;
  }
  .slogan-ribbon svg { position: absolute; inset: 0; }
  .slogan-ribbon span {
    position: absolute; inset: 0; display: flex; align-items: center; justify-content: center;
    color: var(--white); font-weight: 700; font-size: 19px; letter-spacing: 2px;
  }
  .safety-band {
    flex: 1; margin: 0 0 36px; background: var(--rust);
    border-top: 6px solid var(--rust-deep);
    display: flex; justify-content: space-between; padding: 10px 14px 12px;
    color: var(--white);
  }
  .statements { font-size: 8.5px; line-height: 1.35; }
  .statements h2 { font-size: 9.5px; font-weight: 700; margin: 2px 0 3px; }
  .statements ul { list-style: none; margin-bottom: 5px; }
  .statements li::before { content: "• "; }
  .band-right { display: flex; align-items: flex-end; gap: 16px; }
  .pictograms { display: flex; gap: 8px; margin-bottom: 10px; }
  .volume { font-weight: 800; font-size: 64px; line-height: 0.9; }
</style>
</head>
<body>
  <main class="label">
    <header class="product-title">
      <span class="bar"></span>
      <h1>THINNER QXR</h1>
      <span class="bar"></span>
    </header>

    <div class="brand-row">
      <span class="brand-mark"></span>
      <span class="brand-name">ORVANE THINNER</span>
    </div>

    <div class="eagle-illustration" role="img" aria-label="Large stylised orange eagle soaring with wings spread wide"></div>

    <div class="skyline" role="img" aria-label="Cartoon Singapore skyline with the KTR towers, the Corvale wheel and the terrace at the cove">
      <div class="slogan-ribbon">
        <svg viewBox="0 0 346 40" width="346" height="40" aria-hidden="true">
          <path d="M0 4 Q173 16 346 4 L336 20 L346 36 Q173 48 0 36 L10 20 Z" fill="#d9714f"/>
        </svg>
        <span>FLY WITH QUALITY</span>
      </div>
    </div>

    <section class="safety-band">
      <div class="statements">
        <h2>Precautionary</h2>
        <ul>
          <li>Keep Away from Sources of ignition - No Smoking</li>
          <li>Avoid Contact with Eyes</li>
          <li>Do Not Empty into Drains or Sewers</li>
          <li>Take Precautionary Measures Against Static Discharge</li>
        </ul>
        <h2>Hazard</h2>
        <ul>
          <li>Flammable Liquid and Vapor</li>
          <li>May be fatal if swallowed or enters Airways</li>
          <li>Causes Skin Irritation</li>
          <li>Causes Serious Eye Irritation</li>
          <li>Causes Damage to Organs if Prolonged or Repeated Exposure</li>
        </ul>
      </div>
      <div class="band-right">
        <div class="pictograms">
          <svg width="30" height="27" viewBox="0 0 30 27" role="img" aria-label="Flammable hazard"><path d="M15 2 L28 25 H2 Z" fill="#f2c230" stroke="#1e1e1e" stroke-width="2" stroke-linejoin="round"/><path d="M15 10 C18 14 19 17 17 20 H13 C11 17 13 14 15 10 Z" fill="#1e1e1e"/></svg>
          <svg width="30" height="27" viewBox="0 0 30 27" role="img" aria-label="Toxic hazard"><path d="M15 2 L28 25 H2 Z" fill="#f2c230" stroke="#1e1e1e" stroke-width="2" stroke-linejoin="round"/><path d="M10 20 L20 13 M10 13 L20 20" stroke="#1e1e1e" stroke-width="2"/></svg>
          <svg width="30" height="27" viewBox="0 0 30 27" role="img" aria-label="Health hazard"><path d="M15 2 L28 25 H2 Z" fill="#f2c230" stroke="#1e1e1e" stroke-width="2" stroke-linejoin="round"/><circle cx="15" cy="12" r="2.5" fill="#1e1e1e"/><path d="M11 21 L15 15 L19 21 Z" fill="#1e1e1e"/></svg>
        </div>
        <div class="volume">20L</div>
      </div>
    </section>
  </main>
</body>
</html>
```